Create modern and sleek business card for luxury real estate company

We're a "boutique" real estate office looking for a design that gets across a highly modern luxury brand. Blacks and whites are probably the best colors unless we try a silver foil for the logo. I've attached a version of our current logo here. I'd like to swap out the current font on there with Gotham Light Regular.

I'm looking to have one side of the card have the logo with the space for our agents info on the other side.

Target Market(s)

Young professionals in a "luxury" headspace

Industry/Entity Type

Real estate

Contact Information for Business Card

A place for agent name, cell number, website. The slogan "Thoughtfully Redefining Home".

Font styles to use
Other font styles liked:
• Gotham Regular

Colors

Designer to choose only greyscale colors for use in the design.

Requirements
Must have
• Matte black as the background color. Clean lines and use of contrast. A specific design aspect that will use silver foil.
Nice to have
• Up in the air on integrating a QR code
Should not have
• Any houses or other real estate related design (ex: a clip art house)

```html
<!DOCTYPE html>
<html lang="en">
<head>
<meta charset="utf-8">
<title>Meridian Realty – Business Card</title>
<link rel="stylesheet" href="https://fonts.googleapis.com/css2?family=Montserrat:wght@300;400;500&display=swap">
<style>
  :root {
    --backdrop: #b0b1ad;
    --card-matte: #2f2f30;
    --foil-silver: #d9d9d9;
    --text-white: #f2f2f2;
    --text-soft: #c9c9c9;
    --rule: #8a8a8a;
  }
  * { box-sizing: border-box; margin: 0; padding: 0; }
  html, body {
    width: 1200px; height: 801px; overflow: hidden;
    background: var(--backdrop);
    font-family: "Montserrat", Arial, sans-serif;
  }
  .canvas {
    position: relative; width: 1200px; height: 801px;
    display: flex; align-items: center; justify-content: center; gap: 40px;
  }
  .card {
    position: relative; width: 540px; height: 309px;
    background: var(--card-matte);
    border-radius: 18px;
    box-shadow: 0 14px 30px rgba(0,0,0,0.28);
    color: var(--text-white);
  }
  /* Agent side */
  .card--agent { display: flex; align-items: center; padding: 0 36px; }
  .brand { display: flex; align-items: center; gap: 12px; }
  .brand__circle {
    width: 46px; height: 46px; border: 2px solid var(--foil-silver);
    border-radius: 50%; flex: none;
  }
  .brand__name {
    font-weight: 400; color: var(--foil-silver);
    text-transform: uppercase; letter-spacing: 0.08em; line-height: 1.15;
    font-size: 19px;
  }
  .divider {
    width: 1px; height: 110px; background: var(--rule); margin: 0 28px; flex: none;
  }
  .agent__name {
    font-weight: 500; font-size: 17px; letter-spacing: 0.04em; text-transform: uppercase;
  }
  .agent__title { font-weight: 300; font-size: 12px; color: var(--text-soft); margin: 3px 0 12px; }
  .contact { list-style: none; }
  .contact li {
    display: flex; align-items: center; gap: 8px;
    font-weight: 300; font-size: 12px; color: var(--text-soft); margin-bottom: 5px;
  }
  .contact svg { width: 10px; height: 10px; fill: var(--text-soft); flex: none; }
  /* Logo side */
  .card--logo {
    display: flex; flex-direction: column; align-items: center; justify-content: center; gap: 38px;
  }
  .card--logo .brand__circle { width: 74px; height: 74px; }
  .card--logo .brand__name { font-size: 30px; }
  .slogan {
    font-weight: 400; font-size: 15px; letter-spacing: 0.08em; text-transform: uppercase;
  }
</style>
</head>
<body>
<main class="canvas">
  <section class="card card--agent" aria-label="Agent side">
    <div class="brand">
      <span class="brand__circle"></span>
      <span class="brand__name">Meridian<br>Realty</span>
    </div>
    <span class="divider"></span>
    <div class="agent">
      <p class="agent__name">Daniel Hart</p>
      <p class="agent__title">Director</p>
      <ul class="contact">
        <li><svg viewBox="0 0 10 10"><path d="M2 0.5l2 2-1 1.2c.6 1.3 1.6 2.3 2.8 2.8l1.2-1 2 2-1.3 1.8C3.8 8.9 1.1 6.2.3 1.8z"/></svg>555.014.2290</li>
        <li><svg viewBox="0 0 10 10"><path d="M0 2h10v6H0z M0.8 2.6L5 5.6l4.2-3" fill="none" stroke="#c9c9c9" stroke-width="1"/></svg>hello@meridianrealty.com</li>
        <li><svg viewBox="0 0 10 10"><circle cx="5" cy="5" r="4.4"/></svg>www.meridianrealty.com</li>
      </ul>
    </div>
  </section>

  <section class="card card--logo" aria-label="Logo side">
    <div class="brand">
      <span class="brand__circle"></span>
      <span class="brand__name">Meridian<br>Realty</span>
    </div>
    <p class="slogan">Thoughtfully Redefining Home</p>
  </section>
</main>
</body>
</html>
```